BOLD & MINIMALIST DESIGN NEEDED

We want a very bold but minimalistic business card design that is impactful and utilizes both sides of the business card. Our current logo is included for your use.

We want bold fonts and good use of negative space. We don't want the logo to overpower the design.

Target Market(s)

Professionals who are building new commercial buildings.

Industry/Entity Type

Construction

Contact Information for Business Card

Name, Title, email, office phone, cell phone, website

Font styles to use
Serif
Sans Serif

Requirements
Must have
• Bold design!

```html
<!DOCTYPE html>
<html lang="en">
<head>
<meta charset="utf-8">
<title>Ridgeline Design + Build – Business Card</title>
<link rel="stylesheet" href="https://fonts.googleapis.com/css2?family=Arimo:wght@400;700&display=swap">
<style>
  :root {
    --lime: #8cc63f;
    --lime-light: #b3df7a;
    --ink: #111111;
    --text-grey: #555555;
    --rule-grey: #d4d4d4;
    --paper: #ffffff;
    --backdrop: #e7e7e7;
  }
  * { margin: 0; padding: 0; box-sizing: border-box; }
  html, body {
    width: 1200px; height: 1200px; overflow: hidden;
    background: var(--backdrop);
    font-family: "Arimo", Arial, sans-serif;
  }
  .canvas { position: relative; width: 1200px; height: 1200px; }

  .card { position: absolute; width: 689px; height: 393px; overflow: hidden; }

  /* Front */
  .card-front { left: 267px; top: 159px; background: var(--paper); }
  .brand {
    position: absolute; right: 49px; top: 250px;
    display: flex; align-items: center; gap: 10px;
    color: var(--ink); font-weight: 700; text-transform: uppercase;
  }
  .brand-square { width: 22px; height: 22px; background: var(--ink); }
  .brand-name { font-size: 26px; letter-spacing: 1px; line-height: 1; }
  .brand-name small { display: block; font-size: 12px; letter-spacing: 4px; margin-top: 5px; }

  .person { position: absolute; left: 48px; top: 254px; }
  .person-name { font-size: 27px; font-weight: 700; color: var(--ink); letter-spacing: 0.5px; line-height: 1; }
  .person-title { font-size: 16px; color: var(--lime); margin-top: 6px; }

  .rule { position: absolute; left: 48px; right: 49px; top: 301px; height: 1px; background: var(--rule-grey); }

  .contact { position: absolute; top: 313px; list-style: none; font-size: 16px; color: var(--text-grey); line-height: 20px; }
  .contact li { display: flex; align-items: center; gap: 8px; }
  .contact-phones { left: 48px; }
  .contact-web { right: 49px; text-align: right; }
  .contact-web li { justify-content: flex-end; }
  .icon { width: 14px; height: 14px; fill: var(--ink); flex: none; }

  .stripe-lime { position: absolute; left: 0; right: 0; top: 371px; height: 3px; background: var(--lime); }
  .stripe-ink { position: absolute; left: 0; right: 0; top: 374px; bottom: 0; background: var(--ink); }

  /* Back */
  .card-back {
    left: 262px; top: 653px;
    background: radial-gradient(ellipse 55% 70% at 50% 45%, var(--lime-light) 0%, var(--lime) 100%);
    display: flex; align-items: center; justify-content: center;
  }
  .card-back .brand { position: static; gap: 16px; }
  .card-back .brand-square { width: 38px; height: 38px; }
  .card-back .brand-name { font-size: 52px; letter-spacing: 2px; }
  .card-back .brand-name small { font-size: 22px; letter-spacing: 8px; margin-top: 8px; }
</style>
</head>
<body>
<main class="canvas">

  <section class="card card-front">
    <div class="brand">
      <span class="brand-square"></span>
      <span class="brand-name">Ridgeline<small>Design + Build</small></span>
    </div>

    <div class="person">
      <p class="person-name">PETER HALE</p>
      <p class="person-title">President</p>
    </div>

    <div class="rule"></div>

    <ul class="contact contact-phones">
      <li><svg class="icon" viewBox="0 0 16 16"><path d="M3.6 1.2l2.3 2.6-1.3 2a9 9 0 0 0 5.6 5.6l2-1.3 2.6 2.3-1.5 2.2C7.6 14.6 1.4 8.4 1.4 2.7z"/></svg>555-210-4870</li>
      <li><svg class="icon" viewBox="0 0 16 16"><path d="M4 0h8a1 1 0 0 1 1 1v14a1 1 0 0 1-1 1H4a1 1 0 0 1-1-1V1a1 1 0 0 1 1-1zm.6 1.6v11h6.8v-11zM8 13.3a.9.9 0 1 0 0 1.8.9.9 0 0 0 0-1.8z"/></svg>555-318-9026</li>
    </ul>

    <ul class="contact contact-web">
      <li>info@ridgelinebuild.com<svg class="icon" viewBox="0 0 16 16"><path d="M1 3h14v10H1zm1.4 1.2L8 8.6l5.6-4.4z"/></svg></li>
      <li>www.ridgelinebuild.com<svg class="icon" viewBox="0 0 16 16"><circle cx="8" cy="8" r="7"/><path d="M1 8h14M8 1c-3 3.5-3 10.5 0 14M8 1c3 3.5 3 10.5 0 14" stroke="#fff" stroke-width="1" fill="none"/></svg></li>
    </ul>

    <div class="stripe-lime"></div>
    <div class="stripe-ink"></div>
  </section>

  <section class="card card-back">
    <div class="brand">
      <span class="brand-square"></span>
      <span class="brand-name">Ridgeline<small>Design + Build</small></span>
    </div>
  </section>

</main>
</body>
</html>
```